Quorimo Business Card Design Project

We need a business card design for quorimo.example a company based in Berlin, Germany.

?Quorimo is marketplace that enables people all over the world to monetize and exchange their individual knowledge and language skills through interactive video sessions. User are matched by their interests.

On Quorimo everybody can be student or teacher (seller or buyer).

We would love to see designs that use or main color blue and green. The design should communicate what Quorimo enables - see my notice above.

Looking so forward to your designs
Cheers from Berlin,
Lorenz

Target Market(s)

globally

Industry/Entity Type

Teacher

Requirements
Must have
• Lorenz Hubeck
CEO
Quorimo.example

Quorimo e-Services GmbH
Lindenweg 87
10247 Berlin

Fon: +49 30 418 906 25 17
Mobile: 49 172 54 91 37 6
E-Mail: l.hubeck@quorimo.example
Web: www.quorimo.example

```html
<!DOCTYPE html>
<html lang="en">
<head>
<meta charset="utf-8">
<title>Quorimo Business Card</title>
<link rel="stylesheet" href="https://fonts.googleapis.com/css2?family=Arimo:wght@400;700&display=swap">
<style>
  :root {
    --backdrop: #d9d9d9;
    --card: #ffffff;
    --brand-blue: #1a72b9;
    --brand-sky: #1ea0dc;
    --ink: #3a3a3a;
    --wordmark-grey: #6d6e71;
    --rule: #bdbdbd;
  }
  html, body {
    margin: 0;
    padding: 0;
    overflow: hidden;
  }
  body {
    width: 954px;
    height: 1200px;
    position: relative;
    background: var(--backdrop);
    font-family: "Arimo", Arial, sans-serif;
    color: var(--ink);
  }
  .card {
    position: absolute;
    width: 798px;
    height: 456px;
    background: var(--card);
    border-radius: 26px;
    box-shadow: 0 6px 14px rgba(0,0,0,0.35);
  }
  .card--front { left: 87px; top: 89px; }
  .card--back  { left: 75px; top: 643px; }

  .wordmark {
    position: absolute;
    left: 38px;
    top: 176px;
    display: flex;
    align-items: center;
    gap: 16px;
  }
  .wordmark__square {
    width: 48px;
    height: 48px;
    background: var(--brand-sky);
  }
  .wordmark__name {
    font-size: 60px;
    font-weight: 400;
    color: var(--wordmark-grey);
    line-height: 1;
    letter-spacing: 0.5px;
  }

  .divider {
    position: absolute;
    left: 419px;
    top: 82px;
    width: 1px;
    height: 328px;
    background: var(--rule);
  }

  .details {
    position: absolute;
    left: 440px;
    top: 82px;
  }
  .details__name {
    margin: 0;
    font-size: 34px;
    font-weight: 700;
    color: var(--brand-blue);
    line-height: 1;
  }
  .details__role {
    margin: 8px 0 0;
    font-size: 19px;
    line-height: 1;
  }
  .details__address {
    margin: 45px 0 0;
    font-style: normal;
    font-size: 19px;
    line-height: 25px;
  }
  .details__contact {
    margin: 32px 0 0;
    padding: 0;
    list-style: none;
    font-size: 19px;
    line-height: 25px;
    letter-spacing: 0.6px;
  }
  .details__label {
    color: var(--brand-blue);
  }

  .back-mark {
    position: absolute;
    left: 89px;
    top: 150px;
    display: flex;
    flex-direction: column;
    align-items: center;
    gap: 18px;
  }
  .back-mark__square {
    width: 110px;
    height: 110px;
    background: var(--brand-sky);
  }
  .back-mark__name {
    font-size: 34px;
    color: var(--wordmark-grey);
    line-height: 1;
  }
  .back-url {
    position: absolute;
    left: 389px;
    top: 206px;
    font-size: 34px;
    font-weight: 700;
    color: var(--brand-blue);
    line-height: 1;
  }
</style>
</head>
<body>
  <section class="card card--front">
    <div class="wordmark">
      <span class="wordmark__square"></span>
      <span class="wordmark__name">quorimo</span>
    </div>
    <div class="divider"></div>
    <div class="details">
      <h1 class="details__name">Lorenz Hubeck</h1>
      <p class="details__role">CEO</p>
      <address class="details__address">
        Quorimo e-Services GmbH<br>
        Lindenweg 87<br>
        10247 Berlin
      </address>
      <ul class="details__contact">
        <li><span class="details__label">Fon :</span> +49 30 418 906 25 17</li>
        <li><span class="details__label">Mobile :</span> 49 172 54 91 37 6</li>
        <li><span class="details__label">E-Mail :</span> l.hubeck@quorimo.example</li>
        <li><span class="details__label">Web :</span> www.quorimo.example</li>
      </ul>
    </div>
  </section>

  <section class="card card--back">
    <div class="back-mark">
      <span class="back-mark__square"></span>
      <span class="back-mark__name">quorimo</span>
    </div>
    <p class="back-url">www.quorimo.example</p>
  </section>
</body>
</html>
```